Design a New Business Card for Our Company

We are looking for fresh, unique, and a modern business card that reflects our roots as digital marketing agency focused on SEM.

Industry/Entity Type

Marketing

Contact Information for Business Card

looking for very unique out of the box designs. clean and modern that compliments our logo

Requirements
Must have
• colors should match our logo
• Front should have name, address, email, and phone/fax of the person, phone/fax are the same number
• back should have our url

```html
<!DOCTYPE html>
<html lang="en">
<head>
<meta charset="utf-8">
<title>Loomwell Solutions – Business Card</title>
<link rel="stylesheet" href="https://fonts.googleapis.com/css2?family=Source+Sans+3:ital,wght@0,400;0,600;0,700;1,700&display=swap">
<style>
  :root {
    --stage: #161616;
    --card-white: #ffffff;
    --brand-blue: #6199d1;
    --ink: #2b2b2b;
    --muted-grey: #b3b3b3;
  }
  html, body {
    margin: 0;
    width: 1200px;
    height: 900px;
    overflow: hidden;
    background: var(--stage);
    font-family: "Source Sans 3", "Myriad Pro", sans-serif;
  }
  .card {
    position: absolute;
    top: 170px;
    width: 347px;
    height: 561px;
    box-sizing: border-box;
  }
  .card-front { left: 259px; background: var(--card-white); }
  .card-back  { left: 631px; background: var(--brand-blue); }

  .front-band { position: absolute; left: 86px; width: 169px; }
  .front-band--top { top: 0; height: 44px; }
  .front-band--bottom { bottom: 0; height: 48px; }

  .brand-mark {
    position: absolute;
    top: 60px;
    left: 0;
    width: 100%;
    display: flex;
    flex-direction: column;
    align-items: center;
    gap: 18px;
  }
  .brand-mark__dot {
    width: 150px;
    height: 150px;
    border-radius: 50%;
    background: var(--brand-blue);
  }
  .brand-mark__name {
    font-weight: 700;
    font-size: 22px;
    color: var(--muted-grey);
    letter-spacing: 0.5px;
  }

  .person {
    position: absolute;
    top: 299px;
    width: 100%;
    text-align: center;
  }
  .person__name {
    margin: 0;
    font-weight: 600;
    font-size: 22px;
    color: var(--brand-blue);
    letter-spacing: 0.3px;
    line-height: 28px;
  }
  .person__role {
    margin: 0;
    font-size: 15px;
    color: var(--ink);
    line-height: 24px;
  }

  .contact {
    position: absolute;
    top: 374px;
    width: 100%;
    margin: 0;
    padding: 0;
    list-style: none;
    text-align: center;
    font-size: 15px;
    color: var(--ink);
    line-height: 21px;
  }
  .contact__item { display: flex; justify-content: center; align-items: center; gap: 8px; }
  .contact__icon { width: 12px; height: 10px; fill: var(--brand-blue); }

  .address {
    position: absolute;
    top: 447px;
    width: 100%;
    margin: 0;
    font-style: normal;
    text-align: center;
    font-size: 15px;
    line-height: 17px;
    color: var(--ink);
  }

  .back-brand {
    position: absolute;
    top: 252px;
    left: 0;
    width: 100%;
    display: flex;
    justify-content: center;
    align-items: center;
    gap: 10px;
  }
  .back-brand__dot {
    width: 22px;
    height: 22px;
    border-radius: 50%;
    background: var(--card-white);
  }
  .back-brand__name {
    font-weight: 700;
    font-size: 32px;
    color: var(--card-white);
    line-height: 40px;
  }
  .back-url {
    position: absolute;
    top: 372px;
    width: 100%;
    text-align: center;
    font-weight: 700;
    font-style: italic;
    font-size: 15px;
    color: var(--card-white);
  }
</style>
</head>
<body>
  <section class="card card-front" aria-label="Business card front">
    <svg class="front-band front-band--top" viewBox="0 0 169 44" preserveAspectRatio="none" aria-hidden="true">
      <path d="M0 0 H169 V43 Q84.5 20 0 43 Z" fill="var(--brand-blue)"/>
    </svg>

    <div class="brand-mark">
      <div class="brand-mark__dot"></div>
      <div class="brand-mark__name">Loomwell Solutions</div>
    </div>

    <div class="person">
      <h1 class="person__name">JOHN SMITH</h1>
      <p class="person__role">Managing Director</p>
    </div>

    <ul class="contact">
      <li class="contact__item">
        <svg class="contact__icon" viewBox="0 0 12 10" aria-hidden="true">
          <path d="M0 3 Q6 -1 12 3 L10 4.5 L8 3.5 L8 2.5 Q6 2 4 2.5 L4 3.5 L2 4.5 Z M2.5 5 H9.5 L11 10 H1 Z"/>
        </svg>
        <span>823-456-7890</span>
      </li>
      <li class="contact__item">
        <svg class="contact__icon" viewBox="0 0 12 10" aria-hidden="true">
          <path d="M0 1 H12 V9 H0 Z M0.8 1.6 L6 5.5 L11.2 1.6" stroke="#fff" stroke-width="0.9"/>
        </svg>
        <span>info@youremail.com</span>
      </li>
    </ul>

    <address class="address">
      1234, Address Goes Here<br>
      Country Name, 123456
    </address>

    <svg class="front-band front-band--bottom" viewBox="0 0 169 48" preserveAspectRatio="none" aria-hidden="true">
      <path d="M0 0 Q84.5 18 169 0 V48 H0 Z" fill="var(--brand-blue)"/>
    </svg>
  </section>

  <section class="card card-back" aria-label="Business card back">
    <div class="back-brand">
      <div class="back-brand__dot"></div>
      <div class="back-brand__name">Loomwell Solutions</div>
    </div>
    <div class="back-url">www.loomwell.com</div>
  </section>
</body>
</html>
```